UI/ UX Design for ERP Software

We need a new UX/UI interface for a ERP software for property managers. Our CMMS / ERP solution is made based on responsive design technologies and is coded in PHP.
The overall UX to be similar to Tev Ulna - easy navigation, intuitive menus.

Industry/Entity Type

Property Management

Number of Pages Required

5+ page

Requirements
Must have
• Round dock buttons
Consistent icons across the application
Enough Spacing between buttons/icons/ menu
Consistent Font
Nice to have
• We would like the UX to allow the users to use the application without /minimum training.
Should not have
• we don't want anything that is classic with respect to UX

```html
<!DOCTYPE html>
<html lang="en">
<head>
<meta charset="utf-8">
<title>Active Dashboard</title>
<link href="https://fonts.googleapis.com/css2?family=Arimo:wght@400;500&display=swap" rel="stylesheet">
<style>
:root{
  --sidebar:#0a84fb;
  --sidebar-active:#1bb9fb;
  --header:#06bdfb;
  --pill:#0a84fb;
  --canvas-bg:#d7f1fc;
  --legend-bg:#7dd5f7;
  --card:#f8fafb;
  --col-light:#f2f2f2;
  --col-dark:#c9c9c9;
  --grid:#6b6b6b;
  --bar:#78b3f0;
  --text-dark:#2b2b2b;
  --white:#ffffff;
  --stat-light:#06bdfb;
  --stat-dark:#0a84fb;
}
*{margin:0;padding:0;box-sizing:border-box}
html,body{width:1200px;height:664px;overflow:hidden}
body{font-family:"Arimo",Arial,sans-serif;background:var(--canvas-bg);position:relative;color:var(--text-dark)}

.sidebar{position:absolute;left:0;top:0;width:174px;height:664px;background:var(--sidebar)}
.nav-item{position:absolute;left:6px;height:30px;width:168px;display:flex;align-items:center;color:var(--white);font-size:11.4px}
.nav-item svg{position:absolute;left:4px;width:16px;height:16px;fill:var(--white)}
.nav-item span{position:absolute;left:44px}
.nav-item.active{background:var(--sidebar-active);border-radius:10px 0 0 10px;width:168px}

.header{position:absolute;left:174px;top:0;width:1026px;height:54px;background:var(--header)}
.header-title{position:absolute;left:70px;top:20px;color:var(--white);font-size:14.5px}
.header-home{position:absolute;left:36px;top:17px;width:20px;height:20px;fill:var(--white)}
.pill{position:absolute;top:14px;height:27px;border-radius:9px;background:var(--pill);color:var(--white);font-size:10.8px;display:flex;align-items:center}
.pill svg{fill:var(--white)}
.pill-date{left:697px;width:181px}
.pill-range{left:891px;width:121px}

.chart-card{position:absolute;left:200px;top:79px;width:818px;height:475px;background:var(--card);border-radius:16px;box-shadow:0 1px 4px rgba(0,0,0,.08)}
.chart{position:absolute;left:0;top:0}
.axis-label{font-size:10px;fill:var(--text-dark)}

.stats{position:absolute;left:1043px;top:81px;width:157px;height:473px;border-radius:14px 0 0 14px;overflow:hidden}
.stat{height:94.6px;display:flex;flex-direction:column;align-items:center;justify-content:center;color:var(--white)}
.stat:nth-child(odd){background:var(--stat-light)}
.stat:nth-child(even){background:var(--stat-dark)}
.stat-value{font-size:15.5px;margin-bottom:6px}
.stat-label{font-size:11px;display:flex;align-items:center;gap:6px}
.stat-label svg{width:14px;height:14px}

.legend{position:absolute;left:174px;top:580px;width:1026px;height:84px;background:var(--legend-bg)}
.legend-item{position:absolute;display:flex;align-items:center;font-size:11.2px;color:var(--text-dark)}
.legend-dot{width:15px;height:15px;border-radius:50%;margin-right:10px;border:1px solid rgba(255,255,255,.5)}
</style>
</head>
<body>

<nav class="sidebar">
  <div class="nav-item active" style="top:6px"><svg viewBox="0 0 16 16"><path d="M8 1 1 8h2v7h4v-4h2v4h4V8h2z"/></svg><span>Dashboard</span></div>
  <div class="nav-item" style="top:36px"><svg viewBox="0 0 16 16"><circle cx="5" cy="5" r="3"/><circle cx="11" cy="5" r="2.5"/><path d="M0 14c0-4 10-4 10 0zM9 10c3-2 7-1 7 4h-5z"/></svg><span>Customers</span></div>
  <div class="nav-item" style="top:66px"><svg viewBox="0 0 16 16"><path d="M8 1 0 8h2l6-5 6 5h2zM3 9v6h4v-4h2v4h4V9L8 5z"/></svg><span>Properties</span></div>
  <div class="nav-item" style="top:95px"><svg viewBox="0 0 16 16"><path d="M8 1a7 7 0 1 0 0 14A7 7 0 0 0 8 1zm0 3a2.5 2.5 0 1 1 0 5 2.5 2.5 0 0 1 0-5zm0 10a5.5 5.5 0 0 1-4.3-2c1-2 7.6-2 8.6 0A5.5 5.5 0 0 1 8 14z"/></svg><span>Tenants</span></div>
  <div class="nav-item" style="top:125px"><svg viewBox="0 0 16 16"><circle cx="8" cy="5" r="4"/><path d="M2 15c0-5 12-5 12 0z"/></svg><span>Contacts</span></div>
  <div class="nav-item" style="top:154px"><svg viewBox="0 0 16 16"><circle cx="5" cy="6" r="4"/><circle cx="12" cy="12" r="3"/><circle cx="5" cy="6" r="1.5" fill="#0a84fb"/><circle cx="12" cy="12" r="1" fill="#0a84fb"/></svg><span>Contractors</span></div>
  <div class="nav-item" style="top:184px"><svg viewBox="0 0 16 16"><circle cx="8" cy="4" r="2.5"/><circle cx="3" cy="6" r="2"/><circle cx="13" cy="6" r="2"/><path d="M3 14c0-5 10-5 10 0zM0 13c0-3 3-4 4-3zM16 13c0-3-3-4-4-3z"/></svg><span>Employees</span></div>
  <div class="nav-item" style="top:214px"><svg viewBox="0 0 16 16"><path d="M2 2h12v12H2zm2 3v1h8V5zm0 3v1h8V8zm0 3v1h6v-1z"/></svg><span>Prevents,Maintenance</span></div>
  <div class="nav-item" style="top:243px"><svg viewBox="0 0 16 16"><circle cx="6" cy="6" r="5"/><circle cx="12" cy="12" r="3.5"/><circle cx="6" cy="6" r="2" fill="#0a84fb"/></svg><span>Work Orders</span></div>
  <div class="nav-item" style="top:273px"><svg viewBox="0 0 16 16"><path d="M3 5h10l-1 10H4zM6 5V3a2 2 0 0 1 4 0v2H9V3a1 1 0 0 0-2 0v2z"/></svg><span>Purchase Orders</span></div>
  <div class="nav-item" style="top:302px"><svg viewBox="0 0 16 16"><path d="M1 1h2v12h12v2H1z"/><circle cx="9" cy="7" r="3.5"/><path d="M11 9l4 4-1 1-4-4z"/></svg><span>Proerties Inspections</span></div>
  <div class="nav-item" style="top:332px"><svg viewBox="0 0 16 16"><path d="M1 14h15v1H1zM2 8h2v6H2zm3-5h2v11H5zm3 4h2v7H8zm3 3h2v4h-2z"/></svg><span>Energy Management</span></div>
  <div class="nav-item" style="top:361px"><svg viewBox="0 0 16 16"><path d="M8 1 0 15h16zM7 6h2v5H7zm0 6h2v2H7z"/></svg><span>Risk Mangement</span></div>
  <div class="nav-item" style="top:391px"><svg viewBox="0 0 16 16"><path d="M1 2h2v2H1zm4 0h10v2H5zM1 7h2v2H1zm4 0h10v2H5zm-4 5h2v2H1zm4 0h10v2H5z"/></svg><span>Project Management</span></div>
  <div class="nav-item" style="top:421px"><svg viewBox="0 0 16 16"><circle cx="7" cy="9" r="6"/><circle cx="11" cy="6" r="5" fill="none" stroke="#fff" stroke-width="1.5"/><circle cx="7" cy="9" r="3" fill="#0a84fb"/></svg><span>Finacial-Budgeting</span></div>
  <div class="nav-item" style="top:450px"><svg viewBox="0 0 16 16"><path d="M1 2h14v9H6l-4 3v-3H1z"/><circle cx="5" cy="6.5" r="1" fill="#0a84fb"/><circle cx="8" cy="6.5" r="1" fill="#0a84fb"/><circle cx="11" cy="6.5" r="1" fill="#0a84fb"/></svg><span>Tenants Requests</span></div>
  <div class="nav-item" style="top:480px"><svg viewBox="0 0 16 16"><path d="M3 1h10v14H3zm2 3v1h6V4zm0 3v1h6V7zm0 3v1h4v-1z"/></svg><span>Repors</span></div>
  <div class="nav-item" style="top:509px"><svg viewBox="0 0 16 16"><path d="M1 14h15v1H1zM1 11l4-5 3 3 4-5 3 2v2l-3-2-4 5-3-3-4 5z"/></svg><span>Visual Reports</span></div>
  <div class="nav-item" style="top:539px"><svg viewBox="0 0 16 16"><path d="M4 3h5l1 1h5v10H4z"/><path d="M1 6h2v10h10v-1H2V6z"/></svg><span>Files</span></div>
  <div class="nav-item" style="top:568px"><svg viewBox="0 0 16 16"><path d="M3 1h7l3 3v11H3zm2 6v1h6V7zm0 3v1h6v-1zm0 3v1h4v-1z"/></svg><span>pages</span></div>
  <div class="nav-item" style="top:598px"><svg viewBox="0 0 16 16"><circle cx="6" cy="10" r="5"/><circle cx="12" cy="4" r="3"/><circle cx="6" cy="10" r="2" fill="#0a84fb"/></svg><span>Configurations</span></div>
  <div class="nav-item" style="top:628px"><svg viewBox="0 0 16 16"><path d="M2 3l2-2 11 11-2 2zM13 1l2 2-4 4-2-2zM1 13l4-4 2 2-4 4z"/></svg><span>Settings</span></div>
</nav>

<header class="header">
  <svg class="header-home" viewBox="0 0 16 16"><path d="M8 1 0 8h2v7h4v-4h4v4h4V8h2z"/></svg>
  <div class="header-title">Active Dashboard</div>
  <div class="pill pill-date">
    <svg viewBox="0 0 16 16" width="14" height="14" style="margin-left:12px"><path d="M1 3h14v12H1zm1 4v7h12V7z"/><path d="M4 1h1v3H4zm7 0h1v3h-1zM3 8h2v2H3zm3 0h2v2H6zm3 0h2v2H9zm3 0h2v2h-2zM3 11h2v2H3zm3 0h2v2H6z"/></svg>
    <span style="margin-left:8px">27/12/2020 - 03/01/2021</span>
    <svg viewBox="0 0 10 8" width="10" height="9" style="margin-left:8px"><path d="M0 0h10L5 8z"/></svg>
  </div>
  <div class="pill pill-range">
    <svg viewBox="0 0 16 16" width="14" height="14" style="margin-left:12px"><path d="M8 1a7 7 0 1 0 0 14A7 7 0 0 0 8 1zm-1 3h2v4l3 2-1 1.5L7 9z"/></svg>
    <span style="margin-left:9px">Last 7 Days</span>
    <svg viewBox="0 0 10 8" width="10" height="9" style="margin-left:10px"><path d="M0 0h10L5 8z"/></svg>
  </div>
</header>

<section class="chart-card">
  <svg class="chart" width="818" height="475" viewBox="200 79 818 475">
    <g class="columns">
      <rect x="268" y="100" width="104" height="410" fill="var(--col-light)"/>
      <rect x="372" y="100" width="104" height="410" fill="var(--col-dark)"/>
      <rect x="476" y="100" width="104" height="410" fill="var(--col-light)"/>
      <rect x="580" y="100" width="104" height="410" fill="var(--col-dark)"/>
      <rect x="684" y="100" width="104" height="410" fill="var(--col-light)"/>
      <rect x="788" y="100" width="104" height="410" fill="var(--col-dark)"/>
      <rect x="892" y="100" width="104" height="410" fill="var(--col-light)"/>
    </g>
    <g class="grid" stroke="var(--grid)" stroke-width="0.6">
      <line x1="268" y1="132.8" x2="1004" y2="132.8"/>
      <line x1="268" y1="208" x2="1004" y2="208"/>
      <line x1="268" y1="283.2" x2="1004" y2="283.2"/>
      <line x1="268" y1="359.2" x2="1004" y2="359.2"/>
      <line x1="268" y1="434.4" x2="1004" y2="434.4"/>
      <line x1="268" y1="510" x2="1004" y2="510"/>
      <line x1="268" y1="100" x2="268" y2="510"/>
    </g>
    <path class="bar" d="M614 510V217a9 9 0 0 1 9-9h5a9 9 0 0 1 9 9v293z" fill="var(--bar)"/>
    <g class="y-ticks axis-label" text-anchor="end">
      <text x="259" y="130">1.25</text>
      <text x="259" y="203">1.00</text>
      <text x="259" y="279">0.75</text>
      <text x="259" y="354">0.50</text>
      <text x="259" y="431">0.25</text>
      <text x="240" y="506">0</text>
    </g>
    <text class="axis-label" transform="translate(221 306) rotate(-90)" text-anchor="middle">Number</text>
    <g class="x-ticks axis-label" text-anchor="middle">
      <text x="320" y="535">27/12/2020</text>
      <text x="424" y="535">28/12/2020</text>
      <text x="528" y="535">29/12/2020</text>
      <text x="632" y="535">30/12/2020</text>
      <text x="736" y="535">31/12/2020</text>
      <text x="840" y="535">01/01/2020</text>
      <text x="944" y="535">02/01/2020</text>
    </g>
  </svg>
</section>

<aside class="stats">
  <div class="stat"><div class="stat-value">3</div><div class="stat-label"><svg viewBox="0 0 16 16"><path d="M8 1a5 5 0 0 0-5 5c0 4 5 9 5 9s5-5 5-9a5 5 0 0 0-5-5z" fill="#fff"/><circle cx="8" cy="6" r="2" fill="var(--stat-light)"/></svg>Propertis</div></div>
  <div class="stat"><div class="stat-value">8</div><div class="stat-label"><svg viewBox="0 0 16 16"><circle cx="8" cy="8" r="7" fill="#fff"/><circle cx="8" cy="6.5" r="2.5" fill="var(--stat-dark)"/><path d="M3.8 12.5c1-2.5 7.4-2.5 8.4 0" stroke="var(--stat-dark)" stroke-width="2" fill="none"/></svg>Tenants</div></div>
  <div class="stat"><div class="stat-value">422,000.00 Sq.ft.</div><div class="stat-label"><svg viewBox="0 0 16 16"><circle cx="8" cy="8" r="6.5" fill="none" stroke="#fff" stroke-width="1.5"/><path d="M4.5 8l2.5 2.5 5-5" stroke="#fff" stroke-width="1.8" fill="none"/></svg>Total Properties Area</div></div>
  <div class="stat"><div class="stat-value">233,500.00 sq.ft</div><div class="stat-label"><svg viewBox="0 0 16 16"><circle cx="8" cy="8" r="6.5" fill="none" stroke="#fff" stroke-width="1.5"/><path d="M4.5 8l2.5 2.5 5-5" stroke="#fff" stroke-width="1.8" fill="none"/></svg>Rented Area</div></div>
  <div class="stat"><div class="stat-value">188,500.00 sq.ft</div><div class="stat-label"><svg viewBox="0 0 16 16"><circle cx="8" cy="8" r="6.5" fill="none" stroke="#fff" stroke-width="1.5"/><path d="M4.5 8l2.5 2.5 5-5" stroke="#fff" stroke-width="1.8" fill="none"/></svg>Vacancies Area</div></div>
</aside>

<footer class="legend">
  <div class="legend-item" style="left:55px;top:17px"><span class="legend-dot" style="background:#78b3f0"></span>Scheduled Maintenance</div>
  <div class="legend-item" style="left:264px;top:16px"><span class="legend-dot" style="background:#8fe878"></span>Completed Scheduled Maintenance</div>
  <div class="legend-item" style="left:556px;top:17px"><span class="legend-dot" style="background:#f5935a"></span>Future Scheduled Maintenance</div>
  <div class="legend-item" style="left:834px;top:17px"><span class="legend-dot" style="background:#3a3a3a"></span>Scheduled Work Orders</div>
  <div class="legend-item" style="left:55px;top:46px"><span class="legend-dot" style="background:#8a8ed8"></span>Completed Work Orders</div>
  <div class="legend-item" style="left:264px;top:48px"><span class="legend-dot" style="background:#ef4a72"></span>Property Inspections in Progress</div>
  <div class="legend-item" style="left:556px;top:48px"><span class="legend-dot" style="background:#ecd04e"></span>Completed Property Inspections</div>
</footer>

</body>
</html>
```